Equipment Finance Specialist I work with companies who need the funds to buy their equipment

I would like a business card that stands out on the shelves. I want to be able to hand it to someone and say WOW. This card should have my logo.
You can put color into it I am very open on design and color

What my company does is we deal with dealerships that sell equipment such as Dump Trucks garbage trucks tractors trailers. Customers get referred to us and depending on their time in business we will ask for the following items

Companies that have been in business for more than two years we have a credit application program up to 250K . With this program we need the following items Credit application filled out(which is what I would like to be able for the customer to click on my website to get.) as well as three current month bank statements.

Deals over 250k we will need the following items

2 years business tax returns
2 years personal tax returns
Profit & Loss statement
Personal Financial Statement

what we do
100% FINANCING
SEASONAL PAYMENTS
LOAN BALLOON PAYMENTS
TRAC LEASING
LOW-INTEREST REFINANCING RATES
DEBT CONSOLIDATION

We specialize in creative financing solutions and offer a variety of reliable, flexible and expandable lending choices.

Target Market(s)

Trucking Companies

Industry/Entity Type

Trucking Company

Contact Information for Business Card

* $250,000 Application only Program
* Loans from $30,000 to 5,000,000
* Competitive Interest Rates

Font styles to use
Serif
Sans Serif

Colors

Designer to choose colors to be used in the design.

Requirements
Must have
• On the back of the card.
• * $250,000 Application only Program
• * Loans from $30,000 to 5,000,000
• My name, email, website. address
• * Competitive Interest Rates
• * 100% Financing
Nice to have
• I want my logo to pop on the card
• My logo is the great one I would like to use
Should not have
• I am up for your creativity as well

```html
<!DOCTYPE html>
<html lang="en">
<head>
<meta charset="utf-8">
<title>Summit Lending – Business Card</title>
<link href="https://fonts.googleapis.com/css2?family=Open+Sans:wght@400;600;700&display=swap" rel="stylesheet">
<style>
  :root{
    --navy:#0d2d72;
    --navy-light:#1d4ea3;
    --navy-deep:#08215a;
    --red:#d3192b;
    --white:#ffffff;
    --stage:#2a2a2c;
  }
  *{margin:0;padding:0;box-sizing:border-box}
  html,body{width:1200px;height:892px;overflow:hidden;background:var(--stage)}
  body{font-family:"Open Sans",Arial,sans-serif;position:relative}

  .card{position:absolute;width:600px;height:343px;overflow:hidden;box-shadow:0 10px 30px rgba(0,0,0,.45)}

  /* Back side */
  .card-back{left:70px;top:70px;background:linear-gradient(150deg,var(--navy-light) 0%,var(--navy) 55%,var(--navy-deep) 100%)}
  .back-emblem{position:absolute;left:70px;top:110px}
  .emblem-circle{width:120px;height:120px;border-radius:50%;background:var(--white)}
  .offer-list{position:absolute;left:270px;top:125px;list-style:none;color:var(--white);font-weight:600;font-size:16px;line-height:22px}
  .offer-list li::before{content:"";display:inline-block;width:6px;height:6px;border-radius:50%;background:var(--white);margin-right:9px;vertical-align:middle}

  /* Front side */
  .card-front{left:530px;top:480px;background:var(--white)}
  .front-brand{position:absolute;left:36px;top:104px;display:flex;align-items:center;gap:12px}
  .front-brand .brand-dot{width:50px;height:50px;border-radius:50%;background:var(--navy);flex:none}
  .front-brand .brand-name{color:var(--navy);font-weight:700;font-size:26px;letter-spacing:.5px;line-height:1;white-space:nowrap}
  .person{position:absolute;right:30px;top:52px;text-align:right}
  .person-name{color:var(--navy);font-weight:700;font-size:22px;letter-spacing:.5px;line-height:1.1;white-space:nowrap}
  .person-title{color:var(--red);font-size:14px;letter-spacing:1px}
  .contact-band{position:absolute;left:220px;top:180px;right:0;bottom:0;background:var(--navy)}
  .band-circle{position:absolute;left:-60px;top:10px;width:140px;height:140px;border-radius:50%;background:var(--navy);border:6px solid var(--white)}
  .contact-list{position:absolute;right:30px;top:20px;list-style:none;color:var(--white);font-size:14.5px;line-height:22px;text-align:right}
  .contact-list li{display:flex;justify-content:flex-end;align-items:center;gap:8px;white-space:nowrap}
  .contact-list svg{width:12px;height:12px;fill:var(--white);flex:none}
  .contact-list .no-icon{padding-right:20px}
</style>
</head>
<body>

  <section class="card card-back" aria-label="Card back">
    <div class="back-emblem">
      <div class="emblem-circle"></div>
    </div>
    <ul class="offer-list">
      <li>$250,000 Application only Program</li>
      <li>Loans from $30,000 to 5,000,000</li>
      <li>Competitive Interest Rates</li>
      <li>100% Financing</li>
    </ul>
  </section>

  <section class="card card-front" aria-label="Card front">
    <div class="front-brand">
      <span class="brand-dot"></span>
      <span class="brand-name">SUMMIT LENDING</span>
    </div>

    <div class="person">
      <div class="person-name">MARK HOLLOWAY</div>
      <div class="person-title">PRESIDENT</div>
    </div>

    <div class="contact-band">
      <div class="band-circle"></div>
      <ul class="contact-list">
        <li class="no-icon">2190 Harbor Ridge Road</li>
        <li>Lakeview, NY 11020
          <svg viewBox="0 0 12 12"><path d="M6 0a4 4 0 0 0-4 4c0 3 4 8 4 8s4-5 4-8a4 4 0 0 0-4-4zm0 5.5A1.5 1.5 0 1 1 6 2.5a1.5 1.5 0 0 1 0 3z"/></svg></li>
        <li>555 0142 7788
          <svg viewBox="0 0 12 12"><path d="M2.5 0.5l2 2-1 1.5a7 7 0 0 0 4.5 4.5l1.5-1 2 2-1.5 2C5 11.5 0.5 7 0.5 2z"/></svg></li>
        <li>mark@summitlending.com
          <svg viewBox="0 0 12 12"><path d="M0 2h12v8H0zM0.8 2.6L6 6.6l5.2-4z" fill-rule="evenodd"/></svg></li>
        <li>www.summitlending.com
          <svg viewBox="0 0 12 12"><circle cx="6" cy="6" r="5.5"/></svg></li>
      </ul>
    </div>
  </section>

</body>
</html>
```